Bright Path Mentoring Brochure

Looking for a tri-fold brochure that can work as a self-mailer and a leave behind piece.

Bright Path Mentoring works with parents and young teens to develop personal capacity; emotional intelligence, resilience, communications skills, goal setting, and a high level of consciousness and attitude control. See our website at www.brightpathmentoring.example.

Cover should be provocative... quote about 46% of entering freshman from the website is powerful

We are talking about a 11"x8.5" opened, 3.7 x 8.5 folded tri-fold... there should be plenty of content on our website... The inside panels could be as follows

left panel could be a graphic and part of "the Story" Head line about 46% of entering freshman taking more than 6 years to get a degree.

Middle and right panels could be the three programs... Attitudinal Assessment, Group coaching on Communication, Value based S.M.A.R.T. goal setting and defeating internal blocks. and One on One Family coaching.

Target Market(s)

Parents and teens in the 9th grade age range

Industry/Entity Type

Communications

Requirements
Must have
• Provocative Title
"Did you know 46% of entering college freshman fail to receive a degree within 6 years?"
Powerful graphics to communicate transformation from anger and conflict between parents and teens to collaboration and cooperation.

```html
<!DOCTYPE html>
<html lang="en">
<head>
<meta charset="utf-8">
<title>Bright Path Mentoring – Tri-fold Brochure</title>
<link href="https://fonts.googleapis.com/css2?family=Open+Sans:ital,wght@0,400;0,600;0,700;1,400&family=Oswald:wght@400;500;600&display=swap" rel="stylesheet">
<style>
:root{
  --bg:#d9d9d9;
  --paper:#ffffff;
  --green:#7ea63a;
  --green-light:#b9d06c;
  --green-dark:#5f8a2a;
  --forest:#2f5d2c;
  --maroon:#76171c;
  --navy:#1f4f86;
  --ink:#333333;
  --charcoal:#2b2b2b;
  --black:#111111;
}
*{margin:0;padding:0;box-sizing:border-box}
html,body{width:934px;height:1200px;overflow:hidden;background:var(--bg)}
body{font-family:"Open Sans",Arial,sans-serif;color:var(--ink);position:relative}
.spread{position:absolute;left:97px;width:740px;height:572px;background:var(--paper);overflow:hidden;box-shadow:0 2px 6px rgba(0,0,0,.18)}
.spread--outside{top:19px}
.spread--inside{top:609px}
.fold{position:absolute;top:0;bottom:0;width:1px;background:rgba(0,0,0,.08)}
.fold--one{left:247px}.fold--two{left:493px}
.brand{font-family:"Open Sans",Arial,sans-serif;font-weight:700;color:var(--forest);display:flex;align-items:center;gap:6px}
.brand__dot{width:12px;height:12px;border-radius:50%;background:var(--green)}

/* outside */
.opener-quote{position:absolute;left:14px;top:26px;width:220px;font-weight:700;font-size:15px;line-height:1.3;color:var(--green)}
.opener-quote .accent{color:var(--maroon)}
.opener-quote .mark{font-family:Georgia,serif;font-size:30px;color:var(--charcoal);line-height:0;vertical-align:-10px}
.attitude-band{position:absolute;left:0;top:184px;width:493px;height:62px;background:linear-gradient(90deg,var(--green-dark),var(--green-light));color:#fff;font-size:11.5px;font-weight:600;padding:10px 14px}
.attitude-band cite{display:block;text-align:right;font-style:normal;margin-right:30px}
.contact{position:absolute;left:247px;top:22px;width:246px;text-align:center}
.contact .brand{justify-content:center;font-size:14px;margin-bottom:16px}
.contact p{font-size:9.5px;font-weight:600;color:var(--green-dark);line-height:1.75;text-transform:uppercase}
.web-bar{position:absolute;left:271px;top:256px;width:222px;height:24px;background:var(--charcoal);color:#fff;font-size:10px;font-weight:600;padding:5px 10px}
.about{position:absolute;left:18px;top:266px;width:118px;font-size:9.5px;line-height:1.75;color:var(--charcoal)}
.teens-photo{position:absolute;left:140px;top:290px;width:335px;height:272px;background:linear-gradient(180deg,#e6e8ea,#9ea6ae 60%,#5d6670)}
.cover{position:absolute;left:493px;top:0;width:247px;height:572px;background:linear-gradient(160deg,var(--green-light),var(--green) 45%,var(--green-dark));text-align:center;font-family:"Oswald",Arial,sans-serif;text-transform:none}
.cover__lead{color:var(--navy);font-size:25px;font-weight:600;margin-top:28px;line-height:1}
.cover__stat{color:#fff;font-size:78px;font-weight:600;line-height:.95}
.cover__small{color:var(--navy);font-size:17px;font-weight:500;line-height:1.1}
.cover__big{color:#fff;font-size:38px;font-weight:600;line-height:1}
.cover__fail{color:#fff;font-size:74px;font-weight:600;line-height:.95}
.cover__mid{color:#fff;font-size:25px;font-weight:500;line-height:1.1}
.cover__end{color:#fff;font-size:36px;font-weight:600;line-height:1.05}
.cover__base{position:absolute;left:0;bottom:0;width:247px;height:210px}
.cover .brand{position:absolute;left:0;right:0;bottom:80px;justify-content:center;font-size:17px;color:var(--charcoal)}

/* inside */
.story{position:absolute;left:0;top:0;width:247px;height:572px}
.story .brand{justify-content:center;font-size:13px;margin-top:30px}
.story__intro{font-size:10.5px;text-align:center;margin:14px 16px 6px;line-height:1.4;color:var(--charcoal)}
.story__quote{font-size:10.5px;font-weight:700;text-align:center;color:var(--navy);margin:4px 16px;line-height:1.35}
.story__note{font-size:10px;text-align:center;margin:8px 16px;line-height:1.4}
.story__band{position:absolute;left:0;top:392px;width:247px;height:180px;background:linear-gradient(180deg,var(--green-light),var(--green));padding:18px 14px 0}
.story__band h2{font-size:15px;font-weight:600;color:#fff;text-align:center;line-height:1.25}
.programs-cta{position:absolute;left:0;bottom:22px;width:230px;height:32px;background:var(--black);color:#fff;font-size:13.5px;font-weight:600;padding:6px 18px}
.programs{position:absolute;left:247px;top:0;width:493px;height:572px;background:linear-gradient(170deg,var(--green-light),var(--green) 55%,var(--green-dark));color:#fff}
.program-bar{position:absolute;left:0;width:493px;height:20px;font-size:12px;font-weight:700;padding:2px 16px}
.program-bar--one{top:36px;background:var(--maroon)}
.program-bar--two{top:122px;background:var(--forest)}
.program-bar--three{top:232px;background:var(--navy)}
.program-copy{position:absolute;left:16px;width:460px;font-size:9.5px;line-height:1.45}
.program-copy--one{top:60px}
.program-copy--two{top:146px}
.program-copy--three{top:258px}
.program-copy h3{font-size:9.5px;font-weight:600;margin-top:8px}
.program-copy p{margin-top:2px}
</style>
</head>
<body>

<section class="spread spread--outside">
  <div class="opener-quote"><span class="mark">“</span> Self-awareness, <span class="accent">emotional intelligence</span> and the right attitude <span class="accent">cannot start early enough!!!!!</span> <span class="mark">”</span></div>

  <div class="contact">
    <div class="brand"><span class="brand__dot"></span>Bright Path Mentoring</div>
    <p>218 Alder Lane<br>Suite 40-B<br>Fairview, VA 20000<br>marktl4success@brightpath.example<br>(555) 014-7290</p>
  </div>

  <blockquote class="attitude-band">"Your attitude, not your aptitude, determines your altitude."<cite>- Dale Whitmore</cite></blockquote>

  <div class="web-bar">www.brightpathmentoring.example</div>

  <p class="about">At Bright Path Mentoring we specialize in helping parents and their high school age kids to understand, appreciate and take effective action to build personal capacity as individuals. We instill the knowledge and skills that bring out the best in everyone and promote success in every aspect of life, for the rest of their lives</p>

  <div class="teens-photo" role="img" aria-label="Photo of five smiling teenagers standing together with backpacks"></div>

  <div class="cover">
    <div class="cover__lead">Did you know</div>
    <div class="cover__stat">46%</div>
    <div class="cover__small">of entering college</div>
    <div class="cover__big">FRESHMAN</div>
    <div class="cover__fail">FAIL</div>
    <div class="cover__mid">to receive a<br>degree within</div>
    <div class="cover__end">6 years?</div>
    <svg class="cover__base" viewBox="0 0 247 210" aria-hidden="true">
      <path d="M0 40 Q120 10 247 0 L247 210 L0 210 Z" fill="#ffffff"/>
      <path d="M20 36 Q130 2 247 6" fill="none" stroke="#5f8a2a" stroke-width="5"/>
    </svg>
    <div class="brand"><span class="brand__dot"></span>Bright Path Mentoring</div>
  </div>

  <span class="fold fold--one"></span><span class="fold fold--two"></span>
</section>

<section class="spread spread--inside">
  <div class="story">
    <div class="brand"><span class="brand__dot"></span>Bright Path Mentoring</div>
    <p class="story__intro">Ask business executives to describe their recent entry-level hires and you may well hear statements like this…</p>
    <p class="story__quote">"Academically superior, emotionally inferior"</p>
    <p class="story__quote">"Lack patience and persistence; easily thrown off their game"</p>
    <p class="story__quote">"Work to live, don't live to work; disengage when things don't go their way"</p>
    <p class="story__quote">"Do not understand the concept of no I in team"</p>
    <p class="story__note">It's not the recent grads' fault. They are behaving exactly as they were prepared to behave.</p>
    <div class="story__band"><h2>Academic preparation is not the culprit; the lack of emotional and attitudinal preparation is.</h2></div>
    <div class="programs-cta">Check out our programs</div>
  </div>

  <div class="programs">
    <div class="program-bar program-bar--one">Program 1: Assessment</div>
    <div class="program-copy program-copy--one"><p>The Bright Path Mentoring process begins with a comprehensive attitudinal assessment of each team member individually, and the team as a whole. Using the highly respected Core Outlook Index (COI) assessment tool we determine each person's default attitudinal response under normal conditions and under stress. We produce a similar determination for the team as a whole.</p></div>

    <div class="program-bar program-bar--two">Program 2: Personal Coaching</div>
    <div class="program-copy program-copy--two"><p>45-minute weekly one-on-one telephone call with teen<br>45-minute bi-weekly call with one or both parents<br>1-hour monthly in-person meeting with the team<br>The agenda for each call is determined by the client. The coach will provide an agenda "thought starter" via e-mail prior to each call to encourage the client to think about what outcomes they want from the call. Some calls will result in a short assignment which the participant is encouraged to complete.</p></div>

    <div class="program-bar program-bar--three">Program 3 : Group Coaching</div>
    <div class="program-copy program-copy--three">
      <h3>Session 1<br>Effective Communication Workshop</h3>
      <p>Learn About Active Listening. Learn How to Communicate Authentically. Learn the 10 keys to sustaining effective, ongoing communications.</p>
      <h3>Session 2<br>Goal Setting Workshop</h3>
      <p>Using the SMART goal setting framework we enable program participants to set effective goals - both large and small - and hold themselves accountable for attaining them.</p>
      <h3>Session 3<br>Breaking Through Personal Blocks</h3>
      <p>The group learns how to identify self-created obstacles that stand in the way of reaching their desired outcomes. Through role playing and group experiences we develop strategies for removing blocks and moving forward.</p>
    </div>
  </div>

  <span class="fold fold--one"></span><span class="fold fold--two"></span>
</section>

</body>
</html>
```